Website Design for Employee Moral and Happiness Company

Looking for a clean website design that explains our features in a step by step manner so our visitors know exactly what our site does before logging in.

The site is called "Velrato". See logo design and video for a sample of style and an overview of what we do.

Target Market(s)

Business owners that are looking to retain employees.

Number of Pages Required

1 page

```html
<!DOCTYPE html>
<html lang="en">
<head>
<meta charset="utf-8">
<title>Velrato — Why choose velrato</title>
<link rel="stylesheet" href="https://fonts.googleapis.com/css2?family=Crimson+Pro:wght@700&family=Nunito:wght@400;600;700&display=swap">
<style>
  :root {
    --header-bg: #e8e0d7;
    --page-bg: #f2f2f2;
    --accent: #ff6a00;
    --ink: #1d1d1d;
    --heading: #555555;
    --body: #5c5c5c;
    --illustration-bg: #e7dfd5;
    --illustration-mid: #d9cfc2;
    --rail: #8a8a8a;
    --dot-field: #ebebeb;
  }
  * { margin: 0; padding: 0; box-sizing: border-box; }
  html, body { width: 1200px; height: 698px; overflow: hidden; }
  body {
    background: var(--page-bg);
    font-family: "Nunito", Arial, sans-serif;
    position: relative;
    color: var(--body);
  }
  .site-header {
    position: absolute; left: 0; top: 0; width: 1200px; height: 89px;
    background: var(--header-bg);
    box-shadow: 0 1px 3px rgba(0,0,0,0.06);
  }
  .brand {
    position: absolute; left: 66px; top: 14px;
    font-family: "Crimson Pro", Georgia, serif; font-weight: 700;
    font-size: 44px; line-height: 1; color: var(--ink); letter-spacing: 0.5px;
  }
  .main-nav a {
    position: absolute; top: 34px;
    font-size: 15.5px; color: #3a3a3a; text-decoration: none; line-height: 20px;
  }
  .main-nav a.is-active { color: var(--accent); border-bottom: 1px solid var(--accent); }
  .login {
    position: absolute; left: 906px; top: 34px;
    font-size: 15.5px; color: #3a3a3a; line-height: 20px;
    display: flex; align-items: center; gap: 8px;
  }
  .signup {
    position: absolute; left: 995px; top: 18px; width: 140px; height: 45px;
    border-radius: 23px; background: var(--accent); color: #fff;
    font-weight: 700; font-size: 15.5px; letter-spacing: 0.3px;
    display: flex; align-items: center; justify-content: center;
  }
  .section-title {
    position: absolute; left: 66px; top: 162px;
    font-family: "Crimson Pro", Georgia, serif; font-weight: 700;
    font-size: 35px; color: var(--heading);
  }
  .feature { position: absolute; top: 262px; }
  .feature-art {
    height: 169px;
    background: linear-gradient(135deg, var(--illustration-bg), var(--illustration-mid) 55%, var(--illustration-bg));
  }
  .feature-title {
    margin: 31px 0 0 11px;
    font-family: "Crimson Pro", Georgia, serif; font-weight: 700;
    font-size: 22px; color: var(--heading);
  }
  .feature-text {
    margin: 14px 0 0 11px; width: 320px;
    font-size: 17px; line-height: 30px; color: var(--body);
  }
  .dot-field {
    position: absolute; left: 860px; top: 459px; width: 340px; height: 239px;
    background: linear-gradient(180deg, var(--dot-field), #eeeeee);
  }
  .section-rail { position: absolute; left: 1090px; top: 262px; }
  .rail-label {
    position: absolute; left: 1096px; top: 380px;
    font-size: 11.5px; line-height: 13px; color: var(--ink);
  }
</style>
</head>
<body>
  <header class="site-header">
    <div class="brand">velrato</div>
    <nav class="main-nav">
      <a class="is-active" style="left:278px">Home</a>
      <a style="left:342px">Boring Work Events</a>
      <a style="left:499px">Introducing Velrato</a>
      <a style="left:654px">Why Velrato</a>
      <a style="left:767px">Testimonials</a>
    </nav>
    <div class="login">
      <svg width="13" height="12" viewBox="0 0 13 12" fill="none" stroke="#3a3a3a" stroke-width="1.2">
        <path d="M1 6h7M5.5 3.5 8 6 5.5 8.5M10 1.5h1.5v9H10"/>
      </svg>
      Login
    </div>
    <div class="signup">SIGN UP</div>
  </header>

  <h2 class="section-title">Why choose velrato ?</h2>

  <article class="feature" style="left:67px; width:334px">
    <div class="feature-art" role="img" aria-label="Illustration of pinned photos of smiling coworkers"></div>
    <h3 class="feature-title">1. Boost Workplace Happiness</h3>
    <p class="feature-text">Lorem ipsum dolor sit amet, consectetur adipiscing elit, sed do eiusmod tempor incididunt ut labore accumsan lacus vel facilisis.</p>
  </article>

  <article class="feature" style="left:429px; width:338px">
    <div class="feature-art" role="img" aria-label="Illustration of an employee holding up a profile card"></div>
    <h3 class="feature-title">2. Increase Employee Retention</h3>
    <p class="feature-text">Lorem ipsum dolor sit amet, consectetur adipiscing elit, sed do eiusmod tempor incididunt ut labore accumsan lacus vel facilisis.</p>
  </article>

  <div class="dot-field" role="img" aria-label="Decorative dotted background field"></div>

  <svg class="section-rail" width="110" height="262" viewBox="1090 262 110 262" aria-label="Section navigation">
    <line x1="1175" y1="270" x2="1175" y2="518" stroke="var(--rail)" stroke-width="1.5"/>
    <g fill="var(--page-bg)" stroke="#6f6f6f" stroke-width="1.5">
      <circle cx="1175" cy="270" r="5.5"/>
      <circle cx="1175" cy="311" r="5.5"/>
      <circle cx="1175" cy="352" r="5.5"/>
      <circle cx="1175" cy="435" r="5.5"/>
      <circle cx="1175" cy="476" r="5.5"/>
      <circle cx="1175" cy="518" r="5.5"/>
    </g>
    <circle cx="1175" cy="394" r="11" fill="#bdbdbd"/>
    <circle cx="1175" cy="394" r="6.5" fill="#333333"/>
  </svg>
  <div class="rail-label">Why choose<br>velrato</div>
</body>
</html>
```